Report template for evaluation reports to be used by non designers

We are looking for a report template that meets all the requirements listed in the attached documents. letter head, logo etc have been enclosed. Its important that the colour integrity is kept, but beyond that options are welcome.
Its important that the document is extremely easy to use and that is able to be adapted to include eatables, figures, pictures, text boxes etc and keep the integrity of the template

Target Market(s)

Governments, Civil society organisations and research institutions

Font styles to use
Sans Serif

Colors
6b449b
876aae
c0c0c0
000000

Requirements
Must have
• Clean, professional, not concluded, modern, must be easy to use
Should not have
• too busy, hard to use

```html
<!DOCTYPE html>
<html lang="en">
<head>
<meta charset="utf-8">
<title>Civic Insight Institute – 2018 Annual Report Cover</title>
<link href="https://fonts.googleapis.com/css2?family=Open+Sans:wght@400;600;700;800&display=swap" rel="stylesheet">
<style>
  :root {
    --purple: #6b449b;
    --purple-light: #876aae;
    --silver: #c0c0c0;
    --ink: #000000;
    --ink-soft: #222222;
    --map-grey: #e9e9eb;
    --photo-dark: #6e6e70;
    --photo-light: #c9c9cb;
    --paper: #ffffff;
    --stage: #d9d9db;
  }
  * { margin: 0; padding: 0; box-sizing: border-box; }
  html, body {
    width: 1200px; height: 847px; overflow: hidden;
    background: var(--stage);
    font-family: "Open Sans", Arial, sans-serif;
  }
  .spread { display: flex; width: 1200px; height: 847px; }
  .page { position: relative; width: 600px; height: 847px; background: var(--paper); overflow: hidden; }
  .page svg { position: absolute; inset: 0; }
  .back-cover { border-right: 1px solid #e4e4e4; }

  .brand-name { font-family: "Open Sans", Arial, sans-serif; font-weight: 400; fill: var(--ink-soft); }
  .brand-main { font-size: 46px; letter-spacing: 9px; }
  .brand-sub { font-size: 10.5px; letter-spacing: 4px; }
  .back-cover .brand-main { font-size: 36px; letter-spacing: 7px; }
  .back-cover .brand-sub { font-size: 8.5px; letter-spacing: 3px; }

  .contact-text { font-size: 10px; fill: #555; }
  .intro-heading { font-size: 9px; font-weight: 700; fill: var(--purple); }
  .intro-body { font-size: 7.5px; fill: #9a9a9a; }
  .title-year { font-size: 66px; font-weight: 800; fill: #fff; }
  .title-label { font-size: 26px; font-weight: 700; fill: #fff; }
</style>
</head>
<body>
<main class="spread">

  <!-- Back cover -->
  <section class="page back-cover">
    <svg width="600" height="847" viewBox="0 0 600 847">
      <rect class="band-top" x="0" y="0" width="600" height="14" fill="var(--purple)"/>
      <rect class="band-bottom" x="0" y="833" width="600" height="14" fill="var(--purple)"/>

      <rect class="world-map" x="10" y="150" width="580" height="390" rx="6" fill="var(--map-grey)"
            role="img" aria-label="Faint grey world map"/>

      <g class="brand-lockup">
        <text class="brand-name brand-main" x="300" y="660" text-anchor="middle">CIVIC</text>
        <text class="brand-name brand-sub" x="300" y="680" text-anchor="middle">INSIGHT INSTITUTE</text>
      </g>

      <g class="contact contact-phone">
        <circle cx="150" cy="745" r="28" fill="var(--purple-light)"/>
        <circle cx="150" cy="738" r="6" fill="#fff"/>
        <path d="M138 755 q12 -14 24 0 z" fill="#fff"/>
        <text class="contact-text" x="150" y="795" text-anchor="middle">+41 700 000 000</text>
      </g>

      <g class="contact contact-web">
        <circle cx="300" cy="745" r="28" fill="var(--purple-light)"/>
        <circle cx="302" cy="742" r="7" fill="none" stroke="#fff" stroke-width="2"/>
        <line x1="297" y1="747" x2="290" y2="754" stroke="#fff" stroke-width="2.5" stroke-linecap="round"/>
        <text class="contact-text" x="300" y="795" text-anchor="middle">info@civicinsightinstitute.org</text>
        <text class="contact-text" x="300" y="809" text-anchor="middle">www.civicinsightinstitute.org</text>
      </g>

      <g class="contact contact-address">
        <circle cx="450" cy="745" r="28" fill="var(--purple)"/>
        <path d="M438 746 l12 -11 l12 11 z" fill="#fff"/>
        <rect x="442" y="746" width="16" height="10" fill="#fff"/>
        <rect x="448" y="750" width="4" height="6" fill="var(--purple)"/>
        <text class="contact-text" x="450" y="795" text-anchor="middle">12 Harbour Lane,</text>
        <text class="contact-text" x="450" y="809" text-anchor="middle">Fairview, NZ 50210</text>
      </g>
    </svg>
  </section>

  <!-- Front cover -->
  <section class="page front-cover">
    <svg width="600" height="847" viewBox="0 0 600 847">
      <defs>
        <linearGradient id="photoTone" x1="0" y1="0" x2="1" y2="1">
          <stop offset="0" stop-color="var(--photo-light)"/>
          <stop offset="1" stop-color="var(--photo-dark)"/>
        </linearGradient>
      </defs>

      <rect class="band-top" x="0" y="0" width="600" height="14" fill="var(--purple)"/>

      <g class="intro">
        <path d="M40 38 l9 3 l-9 3 z" fill="var(--purple)"/>
        <text class="intro-heading" x="54" y="45">LOREM IPSUM DOLOR SIT AMET</text>
        <text class="intro-body" x="40" y="60">Our year in review: findings, partnerships and evidence that</text>
        <text class="intro-body" x="40" y="71">shaped public policy across the region, with thanks to every</text>
        <text class="intro-body" x="40" y="82">contributor and partner.</text>
      </g>

      <polygon class="cover-photo" points="40,220 430,14 600,14 600,240 40,650"
               fill="url(#photoTone)" role="img"
               aria-label="Greyscale photograph of a city street with buses and a pedestrian walkway"/>

      <polygon class="title-ribbon" points="40,292 540,262 500,420 40,440"
               fill="var(--purple)" opacity="0.72"/>
      <text class="title-year" x="55" y="368">2018</text>
      <text class="title-label" x="58" y="408">ANNUAL REPORT</text>

      <polygon class="accent-wedge" points="40,650 600,240 600,290 180,705 420,847 0,847 0,650"
               fill="var(--purple)"/>
      <polygon class="accent-shade" points="40,650 600,240 600,258 70,655" fill="#5a3787"/>

      <rect class="band-bottom" x="0" y="833" width="600" height="14" fill="var(--purple)"/>

      <g class="brand-lockup">
        <text class="brand-name brand-main" x="395" y="625" text-anchor="middle">CIVIC</text>
        <text class="brand-name brand-sub" x="395" y="648" text-anchor="middle">INSIGHT INSTITUTE</text>
      </g>
    </svg>
  </section>

</main>
</body>
</html>
```